Electrician Letterhead Design MVR

We need some letterhead for our bills and other papers.
Customer address is on the right side (Swiss format)
A4 format

Design should also be applicable on Cards

Target Market(s)

Private Customers, Small Business

Industry/Entity Type

Electrician

Other font styles liked:
• incised 901

Colors
00AB8E
00BBA5
67D7C9
C6EFE9
E9F9F6

```html
<!DOCTYPE html>
<html lang="en">
<head>
<meta charset="utf-8">
<title>MVR Letterhead</title>
<link rel="stylesheet" href="https://fonts.googleapis.com/css2?family=Lato:wght@400;700&family=Montserrat:wght@500;800&family=Italianno&display=swap">
<style>
  :root {
    --teal: #00ab8e;
    --teal-bright: #00bba5;
    --ink: #2b2b2b;
    --ink-soft: #3a3a3a;
    --paper: #ffffff;
    --backdrop: #e6e8e8;
  }
  * { margin: 0; padding: 0; box-sizing: border-box; }
  html, body {
    width: 1200px; height: 1200px; overflow: hidden;
    background: var(--backdrop);
  }
  .letterhead {
    position: absolute; left: 211px; top: 50px;
    width: 778px; height: 1100px;
    background: var(--paper);
    box-shadow: 0 6px 24px rgba(0,0,0,0.18);
    font-family: "Lato", sans-serif;
    color: var(--ink);
  }
  .brand {
    position: absolute; left: 60px; top: 44px;
    display: flex; align-items: center; gap: 10px;
  }
  .brand-name {
    font-family: "Montserrat", sans-serif;
    font-weight: 800; font-size: 64px; line-height: 1;
    color: var(--teal); letter-spacing: 1px;
  }
  .brand-mark {
    width: 14px; height: 14px; background: var(--teal);
  }
  .contact {
    position: absolute; left: 533px; top: 52px;
    border-left: 2px solid var(--teal);
    padding-left: 8px;
    font-family: "Montserrat", sans-serif;
    font-style: normal;
    font-weight: 500; font-size: 13px; color: var(--ink);
  }
  .contact-address { line-height: 18px; margin-bottom: 8px; }
  .contact-line {
    display: flex; align-items: center; gap: 6px;
    height: 19px;
  }
  .contact-line svg { width: 11px; height: 11px; flex: none; }
  .header-rule {
    position: absolute; left: 60px; right: 60px; top: 170px;
    height: 2px; background: var(--teal);
  }
  .letter {
    position: absolute; left: 60px; right: 60px; top: 250px;
    font-size: 14.5px; line-height: 18px; color: var(--ink-soft);
  }
  .date { margin-bottom: 19px; }
  .recipient-block {
    margin-left: 420px;
    width: 238px;
    font-style: normal;
  }
  .recipient { margin-bottom: 19px; }
  .recipient:last-child { margin-bottom: 0; }
  .salutation {
    font-weight: 700; font-size: 19px; color: var(--ink);
    margin: 24px 0 20px;
  }
  .body-copy p {
    font-size: 13.4px; line-height: 17.5px;
    text-align: justify; margin-bottom: 17px;
  }
  .closing { margin-top: 34px; font-size: 13.5px; }
  .signature {
    font-family: "Italianno", cursive;
    font-size: 46px; line-height: 1; color: var(--ink);
    margin-top: 22px;
  }
</style>
</head>
<body>
  <main class="letterhead">
    <header>
      <div class="brand">
        <span class="brand-name">MVR</span>
        <span class="brand-mark"></span>
      </div>
      <address class="contact">
        <div class="contact-address">52-07 Cedar Lane 9,<br>Fairview, NY 11210</div>
        <div class="contact-line">
          <svg viewBox="0 0 12 12"><path fill="#00ab8e" d="M1 3.5C1 2 2.5 1 3.5 1l1 2.3-1 1c.6 1.4 1.8 2.6 3.2 3.2l1-1L10 7.5c0 1-1 2.5-2.5 2.5C4 10 1 7 1 3.5z"/></svg>
          <span>718-555-0142</span>
        </div>
        <div class="contact-line">
          <svg viewBox="0 0 12 12"><rect x="1" y="2.5" width="10" height="7" fill="#00ab8e"/><path d="M1.5 3l4.5 3.5L10.5 3" fill="none" stroke="#fff" stroke-width="1"/></svg>
          <span>info@mvrmail.com</span>
        </div>
        <div class="contact-line">
          <svg viewBox="0 0 12 12"><circle cx="6" cy="6" r="5" fill="#00ab8e"/><path d="M1 6h10M6 1c-2 2.5-2 7.5 0 10M6 1c2 2.5 2 7.5 0 10" fill="none" stroke="#fff" stroke-width="0.8"/></svg>
          <span>www.mvrelectric.com</span>
        </div>
      </address>
      <div class="header-rule"></div>
    </header>

    <section class="letter">
      <p class="date">Feb-03-2022</p>
      <address class="recipient-block">
        <p class="recipient">Mr, Daniel Hart<br>President</p>
        <p class="recipient">Northgate Holdings<br>45 Harbor Road, Suite# 10<br>City, State, 120023</p>
      </address>
      <p class="salutation">Dear Mr, Daniel</p>
      <div class="body-copy">
        <p>Lorem ipsum dolor sit amet, consectetur adipisicing elit, sed do eiusmod tempor incididunt ut labore et dolore magna aliqua. Ut enim ad minim veniam, quis nostrud exercitation ullamco laboris nisi ut aliquip ex ea commodo consequat. Duis aute irure dolor in reprehenderit in voluptate velit esse cillum dolore eu fugiat nulla pariatur.</p>
        <p>Lorem ipsum dolor sit amet, consectetur adipisicing elit, sed do eiusmod tempor incididunt ut labore et dolore magna aliqua. Ut enim ad minim veniam, quis nostrud exercitation ullamco laboris nisi ut aliquip ex ea commodo consequat. Duis aute irure dolor in reprehenderit in voluptate velit esse cillum dolore eu fugiat nulla pariatur.</p>
        <p>Lorem ipsum dolor sit amet, consectetur adipisicing elit, sed do eiusmod tempor incididunt ut labore et dolore magna aliqua. Ut enim ad minim veniam, quis nostrud exercitation ullamco laboris nisi ut aliquip ex ea commodo consequat.</p>
        <p>Excepteur sint occaecat cupidatat non proident, sunt in culpa qui officia deserunt mollit anim id est laborum. re et dolore magnam aliquam quaerat voluptatem.</p>
      </div>
      <p class="closing">Regards</p>
      <p class="signature">Thomas Reed</p>
    </section>
  </main>
</body>
</html>
```